Professional, Attractive, Simple Website Needed!!

We completed the design for our logo.

We need a website built out around this.

Here are a couple samples of how we want ours formatted.

http://brimvoltco.com

http://www.ravelbeam.com/lp/free-quote?LeadSource=Search%20Engine&ProgramName=searchads&experience=qual&language=en&type=brd&gclid=Xk7PLmqwTRZBNVuEYcaHdFgWsLoPeRtQnMxVbCzJaKiOuYtReWqAsDfGhJkLzXcVbNmQwErTyUiOpAsDfGhJkLzX_wcB

http://quorel.co
Updates

Project Deadline Extended
Reason: Extending this deadline due to our delay in providing designers with content for each page. This is coming in next 24 hours.

Project Deadline Extended
Reason: Due to scheduling conflicts and extended travel delays related to Puerto Rico, the deadline has been extended. Your patience is greatly appreciated.

Project Deadline Extended
Reason: Travel and scheduling conflicts have made it impossible to give this project the thorough review it deserves, therefore I am extending the deadline. Thank you for your patience!

Target Market(s)

Home Owners who earn 60k + household annually

Industry/Entity Type

It Professional

Coding

Coded - Design and coding required

Number of Pages Required

5+ page

Font styles to use
Serif

Colors
34a7d8
9bcb3c

Requirements
Must have
• Simple
• Lead form Entry (Ability for visitor to enter Name, number and address for a quote)
• Sleek Design
• Professional
• Testimonials
• Use color Scheme of Design Logo Attached
Nice to have
• Video when site starts
• Like this
• https://www.vidplexa.com/watch?v=Qm8rTbLw3Np&feature=vidplexa.be
Should not have
• Should not include Commercial solar
• Should not include wind power

```html
<!DOCTYPE html>
<html lang="en">
<head>
<meta charset="utf-8">
<title>Sunhaven Energy</title>
<link href="https://fonts.googleapis.com/css2?family=Raleway:wght@400;500;600;700;800&display=swap" rel="stylesheet">
<style>
:root{
  --green:#9bcb3c;
  --blue:#34a7d8;
  --ink:#2b2b2b;
  --muted:#666;
  --white:#fff;
  --night:#0f1410;
  --footer:#1f1a12;
  --line:rgba(255,255,255,.35);
}
*{box-sizing:border-box;margin:0;padding:0}
html,body{width:1200px;height:2711px;overflow:hidden}
body{position:relative;font-family:'Raleway',sans-serif;color:var(--ink);background:var(--white)}
.abs{position:absolute}

/* hero */
.hero-photo{left:0;top:0;width:1200px;height:660px;
  background:linear-gradient(180deg,#1f3f7a 0%,#3a66a8 35%,#6f8fa0 55%,#5e7a3c 75%,#3c5a22 100%)}
.hero-curve{left:0;top:560px;width:1200px;height:120px}
.brand{left:85px;top:40px;display:flex;align-items:center;gap:12px}
.brand-dot{width:46px;height:46px;border-radius:50%;background:var(--green)}
.brand-name{font-size:22px;font-weight:700;color:var(--green);letter-spacing:.5px}
.nav{left:542px;top:64px;display:flex;gap:0}
.nav a{position:absolute;color:var(--white);font-size:13px;text-decoration:none;white-space:nowrap}
.nav-rule{left:87px;top:146px;width:1024px;height:1px;background:var(--line)}
.welcome{left:87px;top:334px;width:491px;height:186px;background:rgba(20,20,20,.72);text-align:center;color:var(--white)}
.welcome h2{font-size:22px;font-weight:500;margin-top:22px;letter-spacing:1px}
.welcome h1{font-size:41px;font-weight:800;margin-top:4px;letter-spacing:.5px}
.watch{display:flex;align-items:center;justify-content:center;gap:14px;margin-top:12px;font-size:13px;font-weight:700}
.watch-btn{width:44px;height:44px;border-radius:50%;border:2px solid var(--green);display:flex;align-items:center;justify-content:center}
.quote{left:822px;top:188px;width:289px;height:426px;background:rgba(10,10,10,.88)}
.quote-head{background:var(--green);height:90px;display:flex;align-items:center;justify-content:center;text-align:center;font-size:21px;line-height:1.3;color:#222;padding:0 14px}
.field{position:absolute;left:16px;width:257px;border-bottom:1px solid rgba(255,255,255,.3);color:#ddd;font-size:13px;padding-bottom:12px}
.quote-btn{position:absolute;left:16px;top:300px;width:259px;height:49px;background:var(--blue);color:var(--white);font-size:21px;display:flex;align-items:center;justify-content:center;letter-spacing:.5px}

/* headings */
.section-title{left:0;width:1200px;text-align:center;font-size:30px;font-weight:400}
.underline{left:549px;width:102px;height:3px;background:var(--green)}

/* steps */
.step{width:152px;height:152px;margin-left:-76px;margin-top:-76px;border-radius:50%;border:2px dashed #bfdcae}
.step-num{width:36px;height:36px;border-radius:50%;background:var(--green);color:var(--white);font-size:17px;font-weight:600;display:flex;align-items:center;justify-content:center}
.step-label{width:220px;margin-left:-110px;text-align:center;font-size:17px;line-height:1.5;color:#333}

/* testimonials */
.testi-bg{left:0;top:1020px;width:1200px;height:724px;background:radial-gradient(ellipse at 50% 45%,#2f4a2c 0%,#182418 45%,#0c120c 100%)}
.testi-curve{left:0;top:1020px;width:1200px;height:80px}
.quote-text{width:440px;text-align:center;font-size:12px;line-height:1.95;color:#e4e4e4}
.avatar{width:66px;height:66px;border-radius:50%;background:linear-gradient(135deg,#8a7a6a,#4d4038);border:2px solid #fff}
.person{width:300px;text-align:center;font-size:15px;color:var(--blue)}
.cta{left:446px;top:1594px;width:297px;height:56px;background:var(--green);color:var(--white);font-size:17px;display:flex;align-items:center;justify-content:center}

/* posts */
.post{top:1926px;width:490px;height:203px;border:1px solid #ddd;background:var(--white)}
.post-photo{position:absolute;left:0;top:0;width:245px;height:203px}
.post-date{position:absolute;left:147px;top:0;width:98px;height:40px;display:flex;align-items:center;gap:6px;padding-left:10px;color:var(--white)}
.post-date b{font-size:29px;font-weight:700}
.post-date span{font-size:10px;line-height:1.15}
.post-body{position:absolute;left:262px;top:24px;width:212px}
.post-title{font-size:16px;line-height:1.5}
.post-text{font-size:11.5px;line-height:1.6;color:#555;margin-top:12px}
.post-more{font-size:11px;color:#999;margin-top:16px}

/* footer */
.footer{left:0;top:2241px;width:1200px;height:470px;background:radial-gradient(ellipse at 60% 40%,#3a2e1c 0%,#1c170f 55%,#110e09 100%)}
.f-head{top:2314px;font-size:18px;color:var(--white);font-weight:500}
.f-rule{top:2353px;height:1px;background:rgba(255,255,255,.2)}
.f-row{color:#eee;font-size:14px;display:flex;gap:18px;align-items:flex-start}
.f-row svg{flex:none;margin-top:3px}
.social{left:87px;top:2536px;display:flex;gap:8px}
.social i{width:30px;height:30px;border-radius:50%;background:#6f6a60}
.news-text{left:478px;top:2372px;width:240px;font-size:13px;line-height:1.7;color:#ccc}
.news-input{left:477px;top:2450px;width:253px;height:40px;background:var(--white);font-size:11px;color:#999;padding:14px 0 0 20px}
.news-btn{left:477px;top:2504px;width:253px;height:40px;background:var(--green);color:var(--white);font-size:18px;display:flex;align-items:center;justify-content:center}
.links a{position:absolute;left:867px;color:#ddd;font-size:12px;text-decoration:none}
.bottom-rule{left:87px;top:2635px;width:1024px;height:1px;background:rgba(255,255,255,.15)}
.copyright{left:0;top:2666px;width:1200px;text-align:center;font-size:12px;color:#bbb}
</style>
</head>
<body>

<header>
  <div class="abs hero-photo" role="img" aria-label="Mother and child blowing dandelion seeds in a sunny field beside rooftop solar panels"></div>
  <svg class="abs hero-curve" viewBox="0 0 1200 120" preserveAspectRatio="none" aria-hidden="true">
    <path d="M0 100 Q600 -30 1200 100 L1200 120 L0 120 Z" fill="#fff"/>
  </svg>

  <div class="abs brand"><span class="brand-dot"></span><span class="brand-name">SUNHAVEN ENERGY</span></div>

  <nav class="abs nav">
    <a style="left:0">Home</a>
    <a style="left:86px">About Us</a>
    <a style="left:193px">Services</a>
    <a style="left:296px">Testimonials</a>
    <a style="left:423px">Blog</a>
    <a style="left:502px">Contact Us</a>
  </nav>
  <div class="abs nav-rule"></div>

  <div class="abs welcome">
    <h2>WELCOME TO</h2>
    <h1>SUNHAVEN ENERGY</h1>
    <div class="watch">
      <span class="watch-btn"><svg width="16" height="18" viewBox="0 0 16 18"><path d="M2 1 L15 9 L2 17 Z" fill="#9bcb3c"/></svg></span>
      WATCH THIS VIDEO
    </div>
  </div>

  <form class="abs quote">
    <div class="quote-head">Enter your details to see If solar works for you.</div>
    <div class="field" style="top:112px">Name</div>
    <div class="field" style="top:163px">Email</div>
    <div class="field" style="top:213px">Address</div>
    <div class="field" style="top:262px;border:none;border-bottom:1px solid rgba(255,255,255,.3);height:1px;padding:0"></div>
    <div class="quote-btn">GET A QUOTE</div>
  </form>
</header>

<section class="steps">
  <h2 class="abs section-title" style="top:648px">4 Easy Steps To Going Solar</h2>
  <div class="abs underline" style="top:708px"></div>

  <svg class="abs" style="left:0;top:780px" width="1200" height="160" aria-hidden="true">
    <path d="M302 68 Q360 130 400 105" fill="none" stroke="#333" stroke-width="2" stroke-dasharray="7 5"/>
    <path d="M551 105 Q600 80 648 92" fill="none" stroke="#333" stroke-width="2" stroke-dasharray="7 5"/>
    <path d="M799 80 Q850 60 894 66" fill="none" stroke="#333" stroke-width="2" stroke-dasharray="7 5"/>
    <g fill="none" stroke="#34a7d8" stroke-width="2.5">
      <!-- headset -->
      <circle cx="226" cy="68" r="14"/><path d="M208 72 v-6 a18 18 0 0 1 36 0 v6"/><rect x="206" y="88" width="40" height="16" rx="3"/>
      <!-- panel -->
      <rect x="445" y="52" width="60" height="34"/><path d="M460 52v34M475 52v34M490 52v34M445 63h60M445 75h60M475 86v14M462 102h26"/>
      <!-- calendar -->
      <rect x="697" y="50" width="52" height="50" rx="3"/><path d="M697 64h52M707 74h32M707 84h22"/>
      <!-- hourglass -->
      <path d="M954 62h32M954 106h32M958 62 q12 22 0 44M982 62 q-12 22 0 44M970 50 l-4 8 h8 l-4 8"/>
    </g>
  </svg>

  <div class="abs step" style="left:226px;top:858px"></div>
  <div class="abs step" style="left:475px;top:858px"></div>
  <div class="abs step" style="left:723px;top:858px"></div>
  <div class="abs step" style="left:970px;top:858px"></div>
  <div class="abs step-num" style="left:267px;top:789px">01</div>
  <div class="abs step-num" style="left:515px;top:789px">02</div>
  <div class="abs step-num" style="left:763px;top:789px">03</div>
  <div class="abs step-num" style="left:1010px;top:789px">04</div>
  <p class="abs step-label" style="left:226px;top:953px">Speak to a<br>solar consultant</p>
  <p class="abs step-label" style="left:475px;top:953px">We'll design your<br>solar panel system</p>
  <p class="abs step-label" style="left:723px;top:953px">Schedule your<br>1 day install</p>
  <p class="abs step-label" style="left:970px;top:953px">Start saving on your<br>electricity bill</p>
</section>

<section class="testimonials">
  <div class="abs testi-bg" role="img" aria-label="Cupped hands holding a glass globe over green foliage, darkened"></div>
  <svg class="abs testi-curve" viewBox="0 0 1200 80" preserveAspectRatio="none" aria-hidden="true">
    <path d="M0 0 L1200 0 L1200 10 Q600 130 0 10 Z" fill="#fff"/>
  </svg>
  <h2 class="abs section-title" style="top:1183px;color:#fff">Our Thousands of Happy Customers</h2>
  <div class="abs underline" style="top:1243px"></div>

  <p class="abs quote-text" style="left:114px;top:1302px">Lorem Ipsum is simply dummy text of the printing and typesetting industry. Lorem Ipsum has been the industry's standard dummy text ever since the 1500s, when an unknown printer took a galley of type and scrambled it to make a type specimen book.</p>
  <p class="abs quote-text" style="left:644px;top:1302px">Lorem Ipsum is simply dummy text of the printing and typesetting industry. Lorem Ipsum has been the industry's standard dummy text ever since the 1500s, when an unknown printer took a galley of type and scrambled it to make a type specimen book.</p>
  <div class="abs avatar" style="left:302px;top:1405px" role="img" aria-label="Customer portrait"></div>
  <div class="abs avatar" style="left:831px;top:1405px" role="img" aria-label="Customer portrait"></div>
  <div class="abs person" style="left:184px;top:1490px">Marla J Fenwick</div>
  <div class="abs person" style="left:714px;top:1490px">Dorian K Whitlock</div>
  <div class="abs cta">GET STARTED</div>
</section>

<section class="posts">
  <h2 class="abs section-title" style="top:1838px">Latest Posts</h2>
  <div class="abs underline" style="top:1886px"></div>

  <article class="abs post" style="left:85px">
    <div class="post-photo" role="img" aria-label="Installers fitting solar panels on a house roof" style="background:linear-gradient(160deg,#7fa6d6 0%,#2c4f9a 55%,#1c2f66 100%)"></div>
    <div class="post-date" style="background:var(--blue)"><b>16</b><span>August<br>2017</span></div>
    <div class="post-body">
      <h3 class="post-title" style="font-weight:400;color:var(--blue)">The standard Lorem Ipsum passage, used 1500s</h3>
      <p class="post-text">Lorem Ipsum is simply dummy text of the printing and typesetting industry. Lorem Ipsum has been the industry's standard the...</p>
      <p class="post-more" style="color:var(--blue)">Read More &gt;</p>
    </div>
  </article>

  <article class="abs post" style="left:622px">
    <div class="post-photo" role="img" aria-label="Smiling worker in hard hat beside a solar panel" style="background:linear-gradient(160deg,#c9a24a 0%,#6e6a66 45%,#3b4a6a 100%)"></div>
    <div class="post-date" style="background:var(--green)"><b>15</b><span>August<br>2017</span></div>
    <div class="post-body">
      <h3 class="post-title" style="font-weight:400">The standard Lorem Ipsum passage, the 1500s</h3>
      <p class="post-text">Lorem Ipsum is simply dummy text of the printing and typesetting industry. Lorem Ipsum has been the industry's standard the...</p>
      <p class="post-more">Read More &gt;</p>
    </div>
  </article>
</section>

<footer>
  <div class="abs footer" role="img" aria-label="Dim glowing light bulb at dusk"></div>

  <h4 class="abs f-head" style="left:89px">GET IN TOUCH</h4>
  <div class="abs f-rule" style="left:89px;width:242px"></div>
  <div class="abs f-row" style="left:89px;top:2384px">
    <svg width="10" height="14" viewBox="0 0 10 14"><path d="M5 0a5 5 0 0 1 5 5c0 4-5 9-5 9S0 9 0 5a5 5 0 0 1 5-5z" fill="#fff"/><circle cx="5" cy="5" r="2" fill="#1c170f"/></svg>
    <div><div style="font-size:15px">SUNHAVEN ENERGY</div><div style="font-size:13px;margin-top:4px">482 Corvel Lane, Redmont, CA, 95512.</div></div>
  </div>
  <div class="abs f-row" style="left:89px;top:2455px">
    <svg width="12" height="12" viewBox="0 0 12 12"><path d="M2 0l3 3-1.5 2a7 7 0 0 0 3.5 3.5L9 7l3 3-2 2C5 12 0 7 0 2z" fill="#fff"/></svg>
    <span style="font-size:13px">123 456 789</span>
  </div>
  <div class="abs f-row" style="left:89px;top:2500px">
    <svg width="12" height="10" viewBox="0 0 12 10"><rect width="12" height="10" fill="#fff"/><path d="M0 0l6 5 6-5" stroke="#1c170f" fill="none"/></svg>
    <span style="font-size:13px">info@company.com</span>
  </div>
  <div class="abs social"><i></i><i></i><i></i><i></i><i></i></div>

  <h4 class="abs f-head" style="left:475px">NEWSLETTER SIGN UP</h4>
  <div class="abs f-rule" style="left:475px;width:242px"></div>
  <p class="abs news-text">Don't miss our news and updates.<br>Subscribe now!</p>
  <div class="abs news-input">Enter Email</div>
  <div class="abs news-btn">SUBMIT</div>

  <h4 class="abs f-head" style="left:867px">QUICK LINKS</h4>
  <div class="abs f-rule" style="left:867px;width:244px"></div>
  <nav class="links">
    <a style="top:2389px">&gt;&nbsp; Home</a>
    <a style="top:2420px">&gt;&nbsp; About Us</a>
    <a style="top:2451px">&gt;&nbsp; Services</a>
    <a style="top:2482px">&gt;&nbsp; Testimonials</a>
    <a style="top:2513px">&gt;&nbsp; Blog</a>
    <a style="top:2544px">&gt;&nbsp; Contact Us</a>
  </nav>

  <div class="abs bottom-rule"></div>
  <p class="abs copyright">Copyright © 2017. Sunhaven Energy. All rights reserved</p>
</footer>

</body>
</html>
```